Kestrel Facilities Business Card Design

We would now like to design business cards with the new Kestrel Facilities logo

Target Market(s)

Professional

Industry/Entity Type

Professional services

Contact Information for Business Card

Employee name, title, phone number, email address, corporate office address and logo.

Font styles to use
Sans Serif

Colors
0054AA
0677BA
7BADD7
CADEEF
E8F1F8

Requirements
Must have
• My logo
Should not have
• any other pictures or images besides my logo

```html
<!DOCTYPE html>
<html lang="en">
<head>
<meta charset="utf-8">
<title>Kestrel Facilities Business Card</title>
<link rel="stylesheet" href="https://fonts.googleapis.com/css2?family=Montserrat:wght@400;500;700&display=swap">
<style>
  :root {
    --backdrop: #2b2b2d;
    --brand-blue: #3579c0;
    --brand-deep: #2f6fb6;
    --logo-silver: #d4d8de;
    --card-white: #ffffff;
    --ink: #1c1c1e;
  }
  * { box-sizing: border-box; margin: 0; padding: 0; }
  html, body {
    width: 1200px; height: 1012px; overflow: hidden;
    background: var(--backdrop);
    font-family: "Montserrat", sans-serif;
  }
  .canvas { position: relative; width: 1200px; height: 1012px; }
  .card {
    position: absolute; left: 240px; width: 720px; height: 410px;
    overflow: hidden; box-shadow: 0 10px 24px rgba(0,0,0,.45);
  }
  .card-front { top: 70px; background: var(--brand-blue); }
  .card-back { top: 532px; background: var(--card-white); }

  .wordmark { display: flex; align-items: center; gap: 14px; font-weight: 700; letter-spacing: .04em; }
  .wordmark .mark-square { width: 38px; height: 38px; }
  .card-front .wordmark {
    position: absolute; left: 50%; top: 50%; transform: translate(-50%, -50%);
    color: var(--logo-silver); font-size: 40px;
  }
  .card-front .wordmark .mark-square { border: 5px solid var(--logo-silver); }
  .card-back .wordmark {
    position: absolute; left: 240px; top: 66px;
    color: var(--brand-deep); font-size: 30px;
  }
  .card-back .wordmark .mark-square { width: 30px; height: 30px; border: 4px solid var(--brand-deep); }

  .person {
    position: absolute; right: 400px; top: 176px; text-align: right;
  }
  .person-name { color: var(--brand-deep); font-weight: 700; font-size: 22px; letter-spacing: .01em; }
  .person-title { color: var(--ink); font-size: 15px; margin-top: 4px; }
  .divider { position: absolute; left: 340px; top: 166px; width: 2px; height: 76px; background: var(--brand-deep); }

  .contacts { position: absolute; left: 358px; top: 164px; list-style: none; }
  .contacts li { display: flex; align-items: center; gap: 8px; font-size: 15px; color: var(--ink); height: 26px; }
  .contacts svg { width: 14px; height: 14px; fill: var(--brand-deep); flex: none; }

  .address-band {
    position: absolute; left: 0; right: 0; top: 290px; height: 80px;
    background: var(--brand-blue); color: var(--card-white);
    display: flex; align-items: center; justify-content: center;
    font-size: 17px; font-weight: 500; letter-spacing: .01em;
  }
</style>
</head>
<body>
<main class="canvas">
  <section class="card card-front" aria-label="Card front">
    <div class="wordmark"><span class="mark-square"></span><span>Kestrel Facilities</span></div>
  </section>

  <section class="card card-back" aria-label="Card back">
    <div class="wordmark"><span class="mark-square"></span><span>Kestrel Facilities</span></div>

    <div class="person">
      <p class="person-name">DANA WHITFIELD</p>
      <p class="person-title">Co-Founder</p>
    </div>
    <span class="divider"></span>

    <ul class="contacts">
      <li>
        <svg viewBox="0 0 16 16" aria-hidden="true"><path d="M3.5 1.5l2.5 0 1 3.5-1.7 1.2a8 8 0 0 0 4.5 4.5l1.2-1.7 3.5 1v2.5a1.5 1.5 0 0 1-1.5 1.5A12.5 12.5 0 0 1 2 3a1.5 1.5 0 0 1 1.5-1.5z"/></svg>
        +254-372-41596
      </li>
      <li>
        <svg viewBox="0 0 16 16" aria-hidden="true"><path d="M1 3h14v10H1z M1.5 3.5L8 9l6.5-5.5" stroke="#fff" stroke-width="1.2"/></svg>
        info@kestrelfacilities.com
      </li>
      <li>
        <svg viewBox="0 0 16 16" aria-hidden="true"><circle cx="8" cy="8" r="7"/><path d="M1 8h14M8 1c-3 3-3 11 0 14M8 1c3 3 3 11 0 14" stroke="#fff" stroke-width="1" fill="none"/></svg>
        www.kestrelfacilities.com
      </li>
    </ul>

    <div class="address-band">4180 N. Harbor View Road Suite 210 Eastfield.28</div>
  </section>
</main>
</body>
</html>
```